Web Design Project

Brightfold Publishing owns and operates a large number of editorial websites. These websites provides mostly consumers in the financial services space with information and price comparisons for a particular service.

Brightfold Publishing, as the holding company for each of these sites, currently has no website. We need to build a website targeted towards potential partners for our websites. The idea being that when we start a conversation with a partner, they can view our site and obtain some basic information about who we are.

The structure of the site is to be very simple, containing only a brief description about who we are, our contact details and a list of some of our websites:
• CoverVault.net.au
• MotorPolicyCheck.com.au
• DwellingCoverCheck.com.au
• MedicalCoverCheck.com.au
• LegacyCoverCheck.com.au
• JourneyCoverCheck.com.au
• AnimalCoverCheck.com.au
• PrivateLendingCheck.com.au
• MobileCoolingUnit.com.au
• FixedSavingsYield.com.au
• ThriftyHousehold.com.au
• CoinNana.com.au
• TameYourPlastic.com.au
• PurseMinder.com.au
• ThirdPartyClaimsCoverNational.com.au
• Trade-Cover.com.au
• MotorPolicyProviders.com.au
• MedicalCoverProviders.com.au
• DwellingCoverHub.com
• LegacyCoverHub.com
• EarningsShieldCoverHub.com
• MedicalCoverHub.com
• AnimalCoverHub.com
• PrivateLendingHub.com
• ChargePlasticHub.com
• DwellingLendingHub.com
• RetireNestEgg.net.au

The design of the site should say 'Internet company', 'professional', 'fresh thinking'. The design should not look like a corporate site that you would see from any corporate services business with images of people in suits. We are ultimately an Internet business and there should be a unique feel to the site.

We are open to a suggestion of a colour pallet as the holding company does not have an established logo.

Some sites that we like are:

http://www.quillmarsh-studio.co.uk/#home
http://previewbox00.layoutdock.example/wt_52418/index.html
http://previewbox00.layoutdock.example/wordpress_61942/
http://ponderloop.example/
http://www.brindlux.example/
http://www.tobiasvrankel.example/
http://www.slickfrontdoors.example/Corporate/design-ideas-detail.html?id=4197
http://pairmint.example/
http://orvendal.example/

Reason: Hi all, Apologies, but I need to extend the timeline. One of our key stakeholders is away for the next week. There are a few good designs that we have received to date and there are some tweaks that we would like to see before making a final decision. Thank you to everyone that has submitted designs - Have a great new year. Derek

Reason: Sorry to have to delay the deadline on this, but we did not find anything in the designs really resonated with us. We will have a further think about the existing designs that have been submitted and how we can provide more specific feedback to the designers to make some modifications to the designs.

Target Market(s)

We are targeting insurance companies / brokers that we are talking to. The idea is that we show a professional face to them.

Industry/Entity Type

Financial

Requirements
Must have
• Home Page (possibly integrated with About us details)
Contact Us
Our Sites

```html
<!DOCTYPE html>
<html lang="en">
<head>
<meta charset="utf-8">
<title>Brightfold Publishing</title>
<link rel="stylesheet" href="https://fonts.googleapis.com/css2?family=Roboto:wght@300;400;500&family=Gilda+Display&display=swap">
<style>
:root{
  --backdrop:#c8d0db;
  --page:#ffffff;
  --brand:#5a7295;
  --nav-top:#a7b3c6;
  --nav-bottom:#7d8da6;
  --ink:#333333;
  --muted:#6f7f97;
  --band:#666666;
  --band-active:#9aa8bf;
  --rule:#d6d9de;
  --link:#4f6a8f;
  --button-edge:#8d8d8d;
  --footer-top:#8a8a8a;
  --footer-bottom:#1e1e1e;
}
*{margin:0;padding:0;box-sizing:border-box}
html,body{width:1200px;height:750px;overflow:hidden}
body{background:var(--backdrop);font-family:"Roboto",Arial,sans-serif;position:relative}
.page{position:absolute;left:176px;top:0;width:833px;height:750px;background:var(--page)}
.footer{position:absolute;left:0;right:0;bottom:0;height:31px;background:linear-gradient(var(--footer-top),#3a3a3a 40%,var(--footer-bottom))}
.logo{position:absolute;left:41px;top:17px;font-weight:300;font-size:30px;color:var(--brand);letter-spacing:-.4px;white-space:nowrap}
.swatches{position:absolute;left:341px;top:24px;display:flex;height:13px}
.swatches span{width:30px;height:13px}
.nav{position:absolute;left:566px;top:0;width:226px;height:31px;border-radius:0 0 7px 7px;background:linear-gradient(var(--nav-top),var(--nav-bottom));color:#fff;font-size:12px;font-weight:300;text-align:right;padding:8px 10px 0 0;white-space:nowrap}
.nav a{color:#fff;text-decoration:none}
.hero{position:absolute;left:41px;top:83px;width:751px;height:251px;background:linear-gradient(90deg,#eef1f6,#dde4ee);overflow:hidden;border:1px solid #e4e7eb}
.hero-photo{position:absolute;left:263px;top:0;width:488px;height:193px;background:linear-gradient(90deg,rgba(221,228,238,0) 0%,#c5d0df 25%,#aab8cc 60%,#8794a8 100%)}
.hero-title{position:absolute;left:16px;top:12px;font-size:17px;font-weight:400;color:#222;white-space:nowrap}
.hero-text{position:absolute;left:17px;top:43px;width:245px;font-size:10px;line-height:16.7px;color:var(--muted)}
.btn{position:absolute;height:19px;border-radius:4px;border:1px solid var(--button-edge);background:linear-gradient(#f4f4f4,#bdbdbd);font-size:10px;color:#333;padding:3px 0 0 8px;white-space:nowrap}
.btn svg{position:absolute;right:5px;top:4px}
.hero .btn{left:178px;top:145px;width:74px}
.band{position:absolute;left:0;top:193px;width:751px;height:58px;background:var(--band)}
.teaser{position:absolute;top:5px;height:47px;display:flex;align-items:center;padding-left:12px;padding-right:6px;border-radius:3px;color:#fff;font-size:9px;line-height:11px}
.teaser.active{background:var(--band-active);color:#222}
.teaser .thumb{width:34px;height:34px;border:2px solid #fff;margin-right:9px;flex:none}
.teaser b{display:block;font-weight:500}
.sites-title,.about-title{position:absolute;font-family:"Gilda Display",Georgia,serif;font-weight:400;font-size:22px;color:var(--brand);white-space:nowrap}
.sites-title{left:47px;top:357px}
.about-title{left:286px;top:357px}
.sites-box{position:absolute;left:50px;top:397px;width:206px;height:280px;border:1px solid #e3e3e3;border-radius:5px;box-shadow:0 1px 4px rgba(0,0,0,.18);padding:10px 0 0 12px}
.sites{list-style:none}
.sites li{height:18.8px;font-size:10px;color:var(--link);display:flex;align-items:center;white-space:nowrap}
.sites li svg{margin-right:6px;flex:none}
.sites-box .btn{left:105px;top:253px;width:91px}
.rule{position:absolute;left:286px;top:389px;width:506px;height:1px;background:var(--rule)}
.about{position:absolute;left:286px;top:398px;width:497px;font-size:10px;line-height:16.7px;color:var(--ink)}
.about p{margin-bottom:6.7px}
</style>
</head>
<body>
<div class="page">
  <div class="logo">Brightfold Publishing</div>
  <div class="swatches">
    <span style="background:#3d3d40"></span><span style="background:#efefef"></span><span style="background:#d6d6d6"></span><span style="background:#9aaabf"></span><span style="background:#8c8c8c"></span>
  </div>
  <nav class="nav"><a href="#">Home</a> | <a href="#">Our Sites</a> | <a href="#">About</a> | <a href="#">Contat Us</a></nav>

  <section class="hero">
    <div class="hero-photo" role="img" aria-label="Team photograph of five colleagues standing with folded arms in a bright office"></div>
    <h1 class="hero-title">Lorem Ipsum is simply dummy text</h1>
    <p class="hero-text">Lorem Ipsum is simply dummy text of the printing and typesetting industry. Lorem Ipsum has been the industry's standard dummy text ever since the 1500s, when an unknown printer took a galley of type and scrambled it to make a type specimen book.</p>
    <div class="btn">Read More<svg width="10" height="10" viewBox="0 0 10 10"><path d="M2 1l6 4-6 4z" fill="none" stroke="#777"/></svg></div>
    <div class="band">
      <div class="teaser" style="left:32px;width:240px"><div class="thumb" role="img" aria-label="Small photo of a coffee cup" style="background:linear-gradient(#bbb,#555)"></div><div><b>Dummy Text</b>Lorem Ipsum is simply dummy text of the printing and typesetting industry.</div></div>
      <div class="teaser active" style="left:258px;width:221px"><div class="thumb" role="img" aria-label="Small photo of a business team" style="background:linear-gradient(#dfe6ee,#8a9ab0)"></div><div><b>Dummy Text</b>Lorem Ipsum is simply dummy text of the printing and typesetting industry.</div></div>
      <div class="teaser" style="left:495px;width:230px"><div class="thumb" role="img" aria-label="Small photo of a city skyline" style="background:linear-gradient(#ddd,#777)"></div><div><b>Dummy Text</b>Lorem Ipsum is simply dummy text of the printing and typesetting industry.</div></div>
    </div>
  </section>

  <h2 class="sites-title">Our Sites</h2>
  <div class="sites-box">
    <ul class="sites">
      <li><svg width="11" height="11" viewBox="0 0 12 12"><path d="M2.5 7.5a4 4 0 0 1 7-4.5M9.5 4.5a4 4 0 0 1-7 4.5" fill="none" stroke="#5a7295" stroke-width="1.5"/></svg>CoverVault.net.au</li>
      <li><svg width="11" height="11" viewBox="0 0 12 12"><path d="M2.5 7.5a4 4 0 0 1 7-4.5M9.5 4.5a4 4 0 0 1-7 4.5" fill="none" stroke="#5a7295" stroke-width="1.5"/></svg>MotorPolicyCheck.com.au</li>
      <li><svg width="11" height="11" viewBox="0 0 12 12"><path d="M2.5 7.5a4 4 0 0 1 7-4.5M9.5 4.5a4 4 0 0 1-7 4.5" fill="none" stroke="#5a7295" stroke-width="1.5"/></svg>DwellingCoverCheck.com.au</li>
      <li><svg width="11" height="11" viewBox="0 0 12 12"><path d="M2.5 7.5a4 4 0 0 1 7-4.5M9.5 4.5a4 4 0 0 1-7 4.5" fill="none" stroke="#5a7295" stroke-width="1.5"/></svg>MedicalCoverCheck.com.au</li>
      <li><svg width="11" height="11" viewBox="0 0 12 12"><path d="M2.5 7.5a4 4 0 0 1 7-4.5M9.5 4.5a4 4 0 0 1-7 4.5" fill="none" stroke="#5a7295" stroke-width="1.5"/></svg>LegacyCoverCheck.com.au</li>
      <li><svg width="11" height="11" viewBox="0 0 12 12"><path d="M2.5 7.5a4 4 0 0 1 7-4.5M9.5 4.5a4 4 0 0 1-7 4.5" fill="none" stroke="#5a7295" stroke-width="1.5"/></svg>JourneyCoverCheck.com.au</li>
      <li><svg width="11" height="11" viewBox="0 0 12 12"><path d="M2.5 7.5a4 4 0 0 1 7-4.5M9.5 4.5a4 4 0 0 1-7 4.5" fill="none" stroke="#5a7295" stroke-width="1.5"/></svg>AnimalCoverCheck.com.au</li>
      <li><svg width="11" height="11" viewBox="0 0 12 12"><path d="M2.5 7.5a4 4 0 0 1 7-4.5M9.5 4.5a4 4 0 0 1-7 4.5" fill="none" stroke="#5a7295" stroke-width="1.5"/></svg>PrivateLendingCheck.com.au</li>
      <li><svg width="11" height="11" viewBox="0 0 12 12"><path d="M2.5 7.5a4 4 0 0 1 7-4.5M9.5 4.5a4 4 0 0 1-7 4.5" fill="none" stroke="#5a7295" stroke-width="1.5"/></svg>MobileCoolingUnit.com.au</li>
      <li><svg width="11" height="11" viewBox="0 0 12 12"><path d="M2.5 7.5a4 4 0 0 1 7-4.5M9.5 4.5a4 4 0 0 1-7 4.5" fill="none" stroke="#5a7295" stroke-width="1.5"/></svg>FixedSavingsYield.com.au</li>
      <li><svg width="11" height="11" viewBox="0 0 12 12"><path d="M2.5 7.5a4 4 0 0 1 7-4.5M9.5 4.5a4 4 0 0 1-7 4.5" fill="none" stroke="#5a7295" stroke-width="1.5"/></svg>ThriftyHousehold.com.au</li>
      <li><svg width="11" height="11" viewBox="0 0 12 12"><path d="M2.5 7.5a4 4 0 0 1 7-4.5M9.5 4.5a4 4 0 0 1-7 4.5" fill="none" stroke="#5a7295" stroke-width="1.5"/></svg>CoinNana.com.au</li>
      <li><svg width="11" height="11" viewBox="0 0 12 12"><path d="M2.5 7.5a4 4 0 0 1 7-4.5M9.5 4.5a4 4 0 0 1-7 4.5" fill="none" stroke="#5a7295" stroke-width="1.5"/></svg>TameYourPlastic.com.au</li>
    </ul>
    <div class="btn">View All Sites<svg width="10" height="10" viewBox="0 0 10 10"><path d="M2 1l6 4-6 4z" fill="none" stroke="#777"/></svg></div>
  </div>

  <h2 class="about-title">Brightfold Publishing</h2>
  <div class="rule"></div>
  <div class="about">
    <p>Lorem Ipsum is simply dummy text of the printing and typesetting industry. Lorem Ipsum has been the industry's standard dummy text ever since the 1500s, when an unknown printer took a galley of type and scrambled it to make a type specimen book. It has survived not only five centuries, but also the leap into electronic typesetting, remaining essentially unchanged. It was popularised in the 1960s with the release of Transfertype sheets containing Lorem Ipsum passages, and more recently with desktop publishing software like Folio Composer including versions of Lorem Ipsum.</p>
    <p>Lorem Ipsum is simply dummy text of the printing and typesetting industry. Lorem Ipsum has been the industry's standard dummy text ever since the 1500s, when an unknown printer took a galley of type and scrambled it to make a type specimen book. It has survived not only five centuries, but also the leap into electronic typesetting, remaining essentially unchanged. It was popularised in the 1960s with the release of Transfertype sheets containing Lorem Ipsum passages, and more recently with desktop publishing software like Folio Composer including versions of Lorem Ipsum.</p>
    <p>Lorem Ipsum is simply dummy text of the printing and typesetting industry. Lorem Ipsum has been the industry's standard dummy text ever since the 1500s, when an unknown printer took a galley of type and scrambled it to make a type specimen book. It has survived not only five centuries, but also the leap into electronic typesetting, remaining essentially unchanged.</p>
  </div>

  <footer class="footer"></footer>
</div>
</body>
</html>
```